Employee Benefits and Insurance Consulting

We are an existing company with over 30 years experience but are changing our name. We would like a simple design with grey tones.

Industry/Entity Type

Insurance

Contact Information for Business Card

Marlow Benefits Consulting
Gerald P Hollins CEO
5172 Brackenridge Road
Hartwell, TN 37990
gerald@marlowbenefits-example.com
865-412-5593 - O
865-247-3861 - C

```html
<!DOCTYPE html>
<html lang="en">
<head>
<meta charset="utf-8">
<title>Marlow Benefits Consulting – Business Card</title>
<link rel="stylesheet" href="https://fonts.googleapis.com/css2?family=Jost:wght@400;600&family=Source+Sans+3:wght@400;600&display=swap">
<style>
  :root {
    --stage: #161616;
    --card-front: #f3f3f3;
    --brand-red: #c8161c;
    --card-back: #d31414;
    --ink: #1e1e1e;
    --sub-ink: #3a3a3a;
    --rule: #9a9a9a;
    --white: #ffffff;
  }
  * { box-sizing: border-box; margin: 0; padding: 0; }
  html, body { width: 1200px; height: 900px; overflow: hidden; }
  body {
    background: var(--stage);
    position: relative;
    font-family: "Source Sans 3", Arial, sans-serif;
  }
  .card {
    position: absolute;
    top: 184px;
    width: 302px;
    height: 490px;
    border-radius: 13px;
  }
  .card--front { left: 299px; background: var(--card-front); color: var(--ink); }
  .card--back  { left: 646px; background: var(--card-back); }

  .wordmark {
    position: absolute;
    left: 0; right: 0;
    text-align: center;
    font-family: "Jost", "Century Gothic", sans-serif;
  }
  .wordmark__name { display: block; font-weight: 600; font-size: 31px; line-height: 1; }
  .wordmark__sub {
    display: flex;
    align-items: center;
    justify-content: center;
    gap: 8px;
    margin: 5px auto 0;
    font-weight: 400;
    font-size: 12px;
    letter-spacing: 2px;
    line-height: 1;
  }
  .wordmark__sub::before,
  .wordmark__sub::after {
    content: "";
    flex: 1;
    height: 1px;
    background: var(--rule);
  }
  .card--front .wordmark { top: 150px; }
  .card--front .wordmark__name { color: var(--brand-red); }
  .card--front .wordmark__sub { width: 252px; color: var(--sub-ink); }
  .card--back .wordmark { top: 420px; color: var(--white); }
  .card--back .wordmark__name { font-size: 29px; }
  .card--back .wordmark__sub { width: 216px; font-size: 11px; }
  .card--back .wordmark__sub::before,
  .card--back .wordmark__sub::after { background: rgba(255,255,255,.7); }

  .holder {
    position: absolute;
    top: 246px; left: 0; right: 0;
    text-align: center;
    color: var(--brand-red);
    font-weight: 600;
    font-size: 19px;
  }
  .holder__title { font-size: 14px; }

  .contacts {
    position: absolute;
    top: 311px; left: 0; right: 0;
    list-style: none;
    text-align: center;
    font-size: 14px;
    line-height: 20px;
  }
  .contacts li { display: flex; justify-content: center; align-items: center; gap: 5px; }
  .contacts svg { width: 10px; height: 10px; fill: var(--brand-red); }

  .address {
    position: absolute;
    top: 400px; left: 0; right: 0;
    text-align: center;
    font-style: normal;
    font-size: 14px;
    line-height: 18px;
  }
</style>
</head>
<body>
  <section class="card card--front" aria-label="Business card front">
    <div class="wordmark">
      <span class="wordmark__name">Marlow Benefits</span>
      <span class="wordmark__sub">CONSULTING</span>
    </div>

    <p class="holder">Gerald P Hollins - <span class="holder__title">CEO</span></p>

    <ul class="contacts">
      <li>
        <svg viewBox="0 0 10 10" aria-hidden="true"><path d="M2.2 0.5 3.8 2.4 2.9 3.6c.6 1.4 1.9 2.7 3.5 3.5l1.2-.9 1.9 1.6-.9 1.6C4.7 9.2.8 5.3.6 1.4z"/></svg>
        865-247-3861
      </li>
      <li>
        <svg viewBox="0 0 10 10" aria-hidden="true"><rect x="2.5" y="0.3" width="5" height="9.4" rx="1"/></svg>
        865-412-5593
      </li>
      <li>
        <svg viewBox="0 0 10 10" aria-hidden="true"><path d="M0 2h10v6H0z"/><path d="M0 2l5 3.4L10 2" fill="none" stroke="#f3f3f3" stroke-width=".9"/></svg>
        gerald@marlowbenefits-example.com
      </li>
    </ul>

    <address class="address">
      5172 Brackenridge Road<br>
      Hartwell, TN 37990
    </address>
  </section>

  <section class="card card--back" aria-label="Business card back">
    <div class="wordmark">
      <span class="wordmark__name">Marlow Benefits</span>
      <span class="wordmark__sub">CONSULTING</span>
    </div>
  </section>
</body>
</html>
```